BOLD & MINIMALIST DESIGN NEEDED

We want a very bold but minimalistic business card design that is impactful and utilizes both sides of the business card. Our current logo is included for your use.

We want bold fonts and good use of negative space. We don't want the logo to overpower the design.

Target Market(s)

Professionals who are building new commercial buildings.

Industry/Entity Type

Construction

Contact Information for Business Card

Name, Title, email, office phone, cell phone, website

Font styles to use
Serif
Sans Serif

Requirements
Must have
• Bold design!

```html
<!DOCTYPE html>
<html lang="en">
<head>
<meta charset="utf-8">
<title>Summitcrest Business Card</title>
<link href="https://fonts.googleapis.com/css2?family=Montserrat:wght@400;500;800&display=swap" rel="stylesheet">
<style>
  :root {
    --bg: #3a3a3a;
    --card: #1c1c1c;
    --green: #8cc63f;
    --white: #ffffff;
    --muted: #e6e6e6;
  }
  * { box-sizing: border-box; margin: 0; padding: 0; }
  html, body { width: 1200px; height: 791px; overflow: hidden; }
  body {
    background: var(--bg);
    font-family: "Montserrat", Arial, sans-serif;
    display: flex;
    align-items: center;
    justify-content: center;
    gap: 40px;
  }
  .card {
    width: 540px;
    height: 309px;
    background: var(--card);
    border-bottom: 3px solid var(--green);
    border-left: 3px solid var(--green);
    position: relative;
    box-shadow: 0 10px 30px rgba(0,0,0,0.35);
  }
  .brand {
    display: flex;
    align-items: center;
    gap: 12px;
    color: var(--white);
    font-weight: 800;
    text-transform: uppercase;
    letter-spacing: 0.02em;
    white-space: nowrap;
  }
  .brand-mark { background: var(--green); flex: none; }

  /* Contact side */
  .card-contact .brand {
    position: absolute;
    left: 34px;
    top: 172px;
    font-size: 23px;
    gap: 10px;
  }
  .card-contact .brand-mark { width: 15px; height: 15px; }
  .divider {
    position: absolute;
    left: 296px;
    top: 78px;
    width: 2px;
    height: 150px;
    background: var(--green);
  }
  .details {
    position: absolute;
    left: 320px;
    top: 70px;
  }
  .person-name {
    color: var(--green);
    font-weight: 800;
    font-size: 18px;
    letter-spacing: 0.01em;
  }
  .person-title {
    color: var(--muted);
    font-size: 13px;
    margin-top: 2px;
    margin-bottom: 24px;
  }
  .contact-list { list-style: none; }
  .contact-list li {
    display: flex;
    align-items: center;
    gap: 9px;
    color: var(--muted);
    font-size: 13px;
    line-height: 22px;
    white-space: nowrap;
  }
  .contact-list svg { width: 12px; height: 12px; flex: none; }

  /* Logo side */
  .card-logo {
    display: flex;
    align-items: center;
    justify-content: center;
  }
  .card-logo .brand { font-size: 46px; gap: 16px; }
  .card-logo .brand-mark { width: 28px; height: 28px; }
</style>
</head>
<body>
  <section class="card card-contact">
    <div class="brand"><span class="brand-mark"></span>Summitcrest</div>
    <div class="divider"></div>
    <div class="details">
      <div class="person-name">MARCUS TOLLEY</div>
      <div class="person-title">President</div>
      <ul class="contact-list">
        <li>
          <svg viewBox="0 0 24 24" aria-hidden="true"><path fill="var(--green)" d="M6.6 10.8a15 15 0 0 0 6.6 6.6l2.2-2.2c.3-.3.7-.4 1-.2 1.1.4 2.3.6 3.6.6.6 0 1 .4 1 1V20c0 .6-.4 1-1 1A17 17 0 0 1 3 4c0-.6.4-1 1-1h3.5c.6 0 1 .4 1 1 0 1.3.2 2.5.6 3.6.1.3 0 .7-.2 1z"/></svg>
          555-014-2200
        </li>
        <li>
          <svg viewBox="0 0 24 24" aria-hidden="true"><rect x="6" y="2" width="12" height="20" rx="2" fill="none" stroke="var(--white)" stroke-width="2"/><circle cx="12" cy="18" r="1.2" fill="var(--white)"/></svg>
          555-014-2200
        </li>
        <li>
          <svg viewBox="0 0 24 24" aria-hidden="true"><rect x="2" y="5" width="20" height="14" fill="var(--green)"/><path d="M2 5l10 8 10-8" fill="none" stroke="var(--card)" stroke-width="2"/></svg>
          m.tolley@sc-build.com
        </li>
        <li>
          <svg viewBox="0 0 24 24" aria-hidden="true"><circle cx="12" cy="12" r="10" fill="var(--green)"/><path d="M2 12h20M12 2c3 3 3 17 0 20M12 2c-3 3-3 17 0 20" fill="none" stroke="var(--card)" stroke-width="1.5"/></svg>
          www.sc-build.com
        </li>
      </ul>
    </div>
  </section>

  <section class="card card-logo">
    <div class="brand"><span class="brand-mark"></span>Summitcrest</div>
  </section>
</body>
</html>
```